Lawn sign for construction company

Would like this to be a very clean and high end design for luxury homes. We need a yard sign designed that includes the company logo, website, phone number and major service offerings (residential and commercial renovations and maintenance)
The company website is brackwellbuilders.com all other contact info is in the attachments
Target Market(s)
Luxury home owners and business owners
Industry/Entity Type
Construction/Home Improvement
Font styles to use
Other font styles liked:
- See company logo and other graphics included for title text fonts. All other fonts can be standard sans serif.
Colors
0054AA
0677BA
7BADD7
CADEEF
E8F1F8
Requirements
Must have
- Clean, easy to read design, would like 2 sided sign. A main sign side and back side which states “free estimates, and includes the website and phone number. Must also match the color scheme of the provided logo and other company images. Dark Navy blue primary color, gray secondary color, and orange as an accent color.
Nice to have
- 2nd sign side very simple design
Should not have
- Too many graphics limit to 1-3 colors

```html
<!DOCTYPE html>
<html lang="en">
<head>
<meta charset="UTF-8">
<title>Brackwell Builders – Yard Sign, Front and Back</title>
<link rel="stylesheet" href="https://fonts.googleapis.com/css2?family=Oswald:wght@500;600&family=Montserrat:wght@600;700;800&display=swap">
<style>
  :root {
    --navy: #0b1f4a;
    --orange: #f08400;
    --white: #ffffff;
    --gray: #6b6b6b;
    --backdrop: #5c5c5c;
  }
  * { margin: 0; padding: 0; box-sizing: border-box; }
  html, body { width: 1200px; height: 2644px; overflow: hidden; }
  body { background: var(--backdrop); position: relative; }

  .sign {
    position: absolute;
    left: 120px;
    width: 960px;
    height: 730px;
    background: var(--white);
    overflow: hidden;
    box-shadow: 0 10px 30px rgba(0,0,0,.25);
  }
  .sign--front { top: 395px; }
  .sign--back  { top: 1520px; }

  .sign__band { position: absolute; inset: 0; width: 960px; height: 730px; }

  .brand-name {
    position: absolute; top: 170px; left: 0; width: 100%;
    text-align: center;
    font-family: "Oswald", sans-serif; font-weight: 600;
    font-size: 92px; letter-spacing: 2px; line-height: 1;
    color: var(--orange);
  }

  .services { position: absolute; top: 548px; left: 0; width: 100%; text-align: center; }
  .services__primary, .services__secondary {
    font-family: "Oswald", sans-serif; font-weight: 500;
    font-size: 58px; line-height: 1.1; letter-spacing: .5px;
  }
  .services__primary { color: var(--orange); }
  .services__secondary { color: var(--white); }
  .services__list {
    margin-top: 12px;
    font-family: "Montserrat", sans-serif; font-weight: 700;
    font-size: 17px; color: var(--white); letter-spacing: .3px;
  }

  .offer { position: absolute; top: 40px; left: 0; width: 100%; text-align: center; }
  .offer__free {
    font-family: "Montserrat", sans-serif; font-weight: 800;
    font-size: 214px; line-height: 1; letter-spacing: 4px; color: var(--orange);
  }
  .offer__estimates {
    margin-top: 14px;
    font-family: "Montserrat", sans-serif; font-weight: 800;
    font-size: 112px; line-height: 1; color: var(--navy);
  }

  .contact {
    position: absolute; top: 512px; left: 0; width: 100%;
    display: flex; justify-content: center;
  }
  .contact__list { display: flex; flex-direction: column; gap: 6px; }
  .contact__row { display: flex; align-items: center; color: var(--white); font-family: "Montserrat", sans-serif; white-space: nowrap; }
  .contact__icon { width: 44px; height: 44px; margin-right: 40px; flex: none; }
  .contact__web { font-weight: 700; font-size: 46px; line-height: 1.15; }
  .contact__phone { font-weight: 700; font-size: 84px; line-height: 1.05; letter-spacing: 1px; }
  .contact__row--web .contact__icon { width: 40px; height: 40px; margin-right: 50px; margin-left: 2px; }
</style>
</head>
<body>

  <section class="sign sign--front" aria-label="Sign front">
    <svg class="sign__band" viewBox="0 0 960 730" preserveAspectRatio="none" aria-hidden="true">
      <polygon points="0,440 480,520 960,440 960,730 0,730" fill="var(--orange)"/>
      <polygon points="0,472 480,536 960,472 960,730 0,730" fill="var(--navy)"/>
    </svg>
    <div class="brand-name">BRACKWELL BUILDERS</div>
    <div class="services">
      <p class="services__primary">RESIDENTIAL AND COMMERCIAL</p>
      <p class="services__secondary">RENOVATIONS AND MAINTENANCE</p>
      <p class="services__list">GENERAL CONTRACTING | PROPERTY MANAGEMENT | REMODELING</p>
    </div>
  </section>

  <section class="sign sign--back" aria-label="Sign back">
    <svg class="sign__band" viewBox="0 0 960 730" preserveAspectRatio="none" aria-hidden="true">
      <polygon points="0,440 480,520 960,440 960,730 0,730" fill="var(--orange)"/>
      <polygon points="0,472 480,536 960,472 960,730 0,730" fill="var(--navy)"/>
    </svg>
    <div class="offer">
      <p class="offer__free">FREE</p>
      <p class="offer__estimates">ESTIMATES</p>
    </div>
    <div class="contact">
      <div class="contact__list">
        <div class="contact__row contact__row--web">
          <svg class="contact__icon" viewBox="0 0 24 24" aria-hidden="true" fill="none" stroke="var(--orange)" stroke-width="2">
            <circle cx="12" cy="12" r="10"/>
            <ellipse cx="12" cy="12" rx="4.5" ry="10"/>
            <line x1="2" y1="12" x2="22" y2="12"/>
            <line x1="4" y1="7" x2="20" y2="7"/>
            <line x1="4" y1="17" x2="20" y2="17"/>
          </svg>
          <span class="contact__web">brackwellbuilders.com</span>
        </div>
        <div class="contact__row">
          <svg class="contact__icon" viewBox="0 0 24 24" aria-hidden="true">
            <path fill="var(--orange)" d="M6.6 10.8c1.4 2.8 3.8 5.1 6.6 6.6l2.2-2.2c.3-.3.7-.4 1-.2 1.1.4 2.3.6 3.6.6.6 0 1 .4 1 1V20c0 .6-.4 1-1 1C10.6 21 3 13.4 3 4c0-.6.4-1 1-1h3.5c.6 0 1 .4 1 1 0 1.3.2 2.5.6 3.6.1.3 0 .7-.2 1L6.6 10.8z"/>
            <path fill="none" stroke="var(--orange)" stroke-width="1.8" stroke-linecap="round" d="M14 3.5a7 7 0 0 1 6.5 6.5M14 7a3.5 3.5 0 0 1 3 3"/>
          </svg>
          <span class="contact__phone">810-555-0147</span>
        </div>
      </div>
    </div>
  </section>

</body>
</html>
```